Calvanto Group Real Estate Company business cards

New business card design, we are generally happy with the basic layout of the existing front of business card, (feel free to change) but require a head shot photo on the back side.

http://www.calvanto.com.au/

Attached logos, and existing business card

------------------------------

Target Market(s)

Real estate

Industry/Entity Type

Real Estate

Contact Information for Business Card

Standard size double sided

Font styles to use
Other font styles liked:
• Futura

Requirements
Must have
• Photo head shot on the back side
Nice to have
• yes
Should not have
• No

```html
<!DOCTYPE html>
<html lang="en">
<head>
<meta charset="utf-8">
<title>Calvanto Group – Business Cards</title>
<link rel="stylesheet" href="https://fonts.googleapis.com/css2?family=Jost:wght@400;500;600;800&display=swap">
<style>
  :root {
    --purple: #2f2163;
    --orange: #f7941d;
    --white: #ffffff;
    --ink: #2a2450;
    --backdrop: #e9e8ee;
    --photo-light: #eceef3;
    --photo-dark: #2c3650;
  }
  * { box-sizing: border-box; margin: 0; padding: 0; }
  html, body { width: 1200px; height: 900px; overflow: hidden; }
  body {
    background: var(--backdrop);
    font-family: "Jost", "Futura", sans-serif;
    display: flex;
    align-items: center;
    justify-content: center;
    gap: 40px;
  }
  .card {
    position: relative;
    width: 540px;
    height: 309px;
    overflow: hidden;
    box-shadow: 0 10px 30px rgba(0,0,0,.18);
  }

  /* Front */
  .card-front { background: var(--purple); color: var(--white); }
  .front-brand {
    position: absolute;
    left: 0; right: 0; top: 78px;
    text-align: center;
  }
  .brand-name {
    font-size: 54px;
    font-weight: 500;
    letter-spacing: -0.5px;
    line-height: 1;
  }
  .services {
    display: inline-block;
    margin-top: 18px;
    border: 1.5px solid #b9b5cc;
    padding: 2px 10px 3px;
    font-size: 15px;
    font-weight: 600;
    letter-spacing: 2px;
  }
  .services .sep { color: var(--orange); padding: 0 4px; }
  .front-band {
    position: absolute;
    left: 0; right: 0; bottom: 0;
    height: 54px;
    background: var(--orange);
    display: flex;
    align-items: center;
    justify-content: center;
    font-size: 19px;
    letter-spacing: .5px;
  }
  .front-band strong { font-weight: 800; }

  /* Back */
  .card-back { background: var(--white); color: var(--ink); }
  .headshot {
    position: absolute;
    left: 24px; bottom: 0;
    width: 220px; height: 270px;
    background: linear-gradient(180deg, var(--photo-light) 0%, #c9cdd8 40%, var(--photo-dark) 100%);
    border-radius: 110px 110px 0 0;
    z-index: 1;
  }
  .back-band {
    position: absolute;
    left: 0; right: 0; bottom: 0;
    height: 42px;
    background: var(--purple);
    color: var(--white);
    display: flex;
    align-items: center;
    justify-content: flex-end;
    padding-right: 24px;
    font-size: 21px;
    letter-spacing: .5px;
  }
  .contact {
    position: absolute;
    right: 24px; top: 24px;
    text-align: right;
  }
  .contact .brand-name { color: var(--purple); font-size: 40px; }
  .person-name {
    margin-top: 14px;
    font-size: 25px;
    font-weight: 800;
    color: var(--purple);
    line-height: 1;
  }
  .person-role {
    font-size: 13px;
    font-weight: 500;
    color: var(--orange);
    letter-spacing: .5px;
  }
  .details { list-style: none; margin-top: 8px; font-size: 13px; line-height: 1.45; color: var(--ink); }
  .details li { display: flex; align-items: center; justify-content: flex-end; gap: 6px; }
  .details .label { color: var(--orange); }
  .details svg { width: 11px; height: 11px; flex: none; }
  .icon-gap { width: 11px; flex: none; }
</style>
</head>
<body>

  <section class="card card-front" aria-label="Business card front">
    <div class="front-brand">
      <div class="brand-name">Calvanto Group</div>
      <div class="services">Buy<span class="sep">|</span>Sell<span class="sep">|</span>Rent</div>
    </div>
    <div class="front-band">www.<strong>calvanto.com</strong>.au</div>
  </section>

  <section class="card card-back" aria-label="Business card back">
    <div class="headshot" role="img" aria-label="Head shot photo of the director in a navy suit and blue tie"></div>
    <div class="contact">
      <div class="brand-name">Calvanto Group</div>
      <div class="person-name">DANIEL TRAN</div>
      <div class="person-role">DIRECTOR</div>
      <ul class="details">
        <li><span><span class="label">ABN:</span> 42 518 306 927</span><span class="icon-gap"></span></li>
        <li>0412 586 903
          <svg viewBox="0 0 12 12" aria-hidden="true"><rect x="3" y="1" width="6" height="10" rx="1" fill="none" stroke="#f7941d" stroke-width="1.2"/><circle cx="6" cy="9.2" r=".7" fill="#f7941d"/></svg>
        </li>
        <li>daniel.tran@calvanto.com.au
          <svg viewBox="0 0 12 12" aria-hidden="true"><rect x="1" y="2.5" width="10" height="7" fill="none" stroke="#f7941d" stroke-width="1.2"/><path d="M1 2.5 6 6.5 11 2.5" fill="none" stroke="#f7941d" stroke-width="1.2"/></svg>
        </li>
        <li>www.calvanto.com.au
          <svg viewBox="0 0 12 12" aria-hidden="true"><circle cx="6" cy="6" r="4.8" fill="none" stroke="#f7941d" stroke-width="1.2"/><ellipse cx="6" cy="6" rx="2" ry="4.8" fill="none" stroke="#f7941d" stroke-width="1"/><path d="M1.2 6h9.6" stroke="#f7941d" stroke-width="1"/></svg>
        </li>
      </ul>
    </div>
    <div class="back-band">your next move starts here</div>
  </section>

</body>
</html>
```